Sticker for Scrap Metal Bin that is placed at customers premises

During the course of our operation, Scrap Metal Bin are place at our customer site for them to dispose scrap metal into the Bin.

Would like to have a sticker for us to paste on the bin.

All scrap bin will be blue color. Attached sample of current sticker on a scrap bin.

Would like one that is clean, simple and eye catching also that the font is much visible unlike the current one that is cramp and small.

Target Market(s)

Businesses

Font styles to use
Serif

Requirements
Must have
• 1) Company Name and Logo
• 2) Contact Details : 9413 5207 / 6582 3046
• 3) Website: www.korvamelt.com

```html
<!DOCTYPE html>
<html lang="en">
<head>
<meta charset="utf-8">
<title>Korva Melt Recycling – Scrap Metal Bin Sticker</title>
<link rel="stylesheet" href="https://fonts.googleapis.com/css2?family=Krona+One&family=Fjalla+One&display=swap">
<style>
  :root {
    --sticker-white: #ffffff;
    --brand-gold: #c9962e;
    --brand-grey: #7d7d7d;
    --band-yellow: #fdd505;
    --ink: #231f20;
  }
  html, body {
    margin: 0;
    padding: 0;
    width: 1200px;
    height: 800px;
    overflow: hidden;
    background: var(--sticker-white);
  }
  .sticker {
    display: block;
    width: 1200px;
    height: 800px;
  }
  .brand-mark { fill: none; stroke: var(--brand-gold); stroke-width: 5; }
  .brand-name {
    font-family: "Krona One", sans-serif;
    fill: var(--brand-gold);
    font-size: 58px;
  }
  .brand-descriptor {
    font-family: "Krona One", sans-serif;
    fill: var(--brand-grey);
    font-size: 34px;
  }
  .band { fill: var(--band-yellow); }
  .icon-area { fill: var(--ink); }
  .divider { fill: var(--ink); }
  .headline {
    font-family: "Krona One", sans-serif;
    fill: var(--ink);
    font-size: 104px;
  }
  .phone-badge { fill: var(--band-yellow); }
  .phone-glyph { fill: var(--ink); }
  .contact {
    font-family: "Fjalla One", sans-serif;
    fill: var(--ink);
    font-size: 44px;
  }
</style>
</head>
<body>
<svg class="sticker" viewBox="0 0 1200 800" xmlns="http://www.w3.org/2000/svg">
  <!-- Brand header -->
  <g class="brand">
    <rect class="brand-mark" x="524" y="42" width="162" height="158"/>
    <text class="brand-name" x="321" y="299" textLength="573" lengthAdjust="spacingAndGlyphs">KORVA MELT</text>
    <text class="brand-descriptor" x="894" y="348" text-anchor="end" textLength="284" lengthAdjust="spacingAndGlyphs">RECYCLING</text>
  </g>

  <!-- Yellow category band -->
  <rect class="band" x="0" y="374" width="1200" height="308"/>
  <circle class="icon-area" cx="189" cy="529" r="126" role="img" aria-label="Recycling arrows circling a hex bolt"/>
  <rect class="divider" x="338" y="399" width="11" height="275" rx="5"/>
  <text class="headline" x="424" y="489" textLength="642" lengthAdjust="spacingAndGlyphs">SCRAP</text>
  <text class="headline" x="424" y="617" textLength="600" lengthAdjust="spacingAndGlyphs">METAL</text>

  <!-- Contact footer -->
  <g class="contact-row">
    <circle class="phone-badge" cx="92" cy="736" r="34"/>
    <path class="phone-glyph" d="M80 718c2-2 5-2 6 0l5 7c1 2 1 4-1 5l-3 3c2 5 6 9 11 11l3-3c1-2 3-2 5-1l7 5c2 1 2 4 0 6l-4 4c-3 3-8 3-13 0-9-5-16-12-21-21-3-5-3-10 0-13z"/>
    <text class="contact" x="142" y="752">: 9413 5207 / 6582 3046</text>
    <text class="contact" x="1138" y="752" text-anchor="end" textLength="382" lengthAdjust="spacingAndGlyphs">www.korvamelt.com</text>
  </g>
</svg>
</body>
</html>
```